Redesign of business card for Cedar Ridge Mechanical

We are looking for a new design for our business cards for Cedar Ridge Mechanical. We are a plumbing & HVAC construction company, operating on the West Coast of Canada and USA. Logo attached.
Industry/Entity Type
Construction - Plumbing & HVAC
Contact Information for Business Card
Name, address, phone numbers, email, website address
Look and feel
Each slider illustrates characteristics of the customer's brand and the style your logo design should communicate.

```html
<!DOCTYPE html>
<html lang="en">
<head>
<meta charset="utf-8">
<title>Cedar Ridge Mechanical – Business Card</title>
<link href="https://fonts.googleapis.com/css2?family=Montserrat:wght@400;500;700;800&display=swap" rel="stylesheet">
<style>
  :root {
    --backdrop: #3a3a3d;
    --ink: #0b0b0b;
    --paper: #ffffff;
    --muted: #2a2a2a;
    --ghost: #e6e6e6;
  }
  * { margin: 0; padding: 0; box-sizing: border-box; }
  html, body {
    width: 1200px; height: 913px; overflow: hidden;
    background: var(--backdrop);
    font-family: "Montserrat", Arial, sans-serif;
  }
  .canvas { position: relative; width: 1200px; height: 913px; }

  .card {
    position: absolute;
    width: 560px; height: 320px;
    border-radius: 22px;
    overflow: hidden;
  }

  /* Back side */
  .card--back {
    left: 80px; top: 90px;
    background: var(--ink);
    display: flex; align-items: center; justify-content: center;
  }
  .brand {
    display: flex; align-items: center; gap: 14px;
    color: var(--paper);
    font-weight: 700;
    text-transform: uppercase;
    letter-spacing: 0.04em;
  }
  .brand__mark { width: 22px; height: 22px; background: currentColor; }
  .card--back .brand { font-size: 30px; }

  /* Front side */
  .card--front {
    left: 560px; top: 500px;
    background: var(--paper);
    color: var(--ink);
  }
  .front__tab {
    position: absolute; left: 0; top: 96px;
    width: 12px; height: 58px; background: var(--ink);
  }
  .person { position: absolute; left: 34px; top: 96px; }
  .person__name { font-size: 22px; font-weight: 800; letter-spacing: 0.03em; text-transform: uppercase; }
  .person__role { font-size: 15px; font-weight: 400; color: var(--muted); margin-top: 4px; }

  .card--front .brand {
    position: absolute; right: 26px; top: 30px;
    color: var(--ink); font-size: 15px; gap: 8px;
  }
  .card--front .brand__mark { width: 12px; height: 12px; }

  .ghost-name {
    position: absolute; left: 40px; bottom: 34px;
    font-size: 34px; font-weight: 700; text-transform: uppercase;
    letter-spacing: 0.04em; color: var(--ghost);
  }

  .contacts {
    position: absolute; right: 26px; top: 96px;
    list-style: none; text-align: right;
    font-size: 14px; line-height: 1.45; color: var(--muted);
  }
  .contacts li { display: flex; justify-content: flex-end; align-items: center; gap: 8px; }
  .contacts .spacer { height: 12px; }
  .contacts svg { width: 12px; height: 12px; flex: none; }
  .icon-blank { width: 12px; }
</style>
</head>
<body>
<main class="canvas">

  <section class="card card--back" aria-label="Card back">
    <div class="brand"><span class="brand__mark"></span>Cedar Ridge Mechanical</div>
  </section>

  <section class="card card--front" aria-label="Card front">
    <div class="brand"><span class="brand__mark"></span>Cedar Ridge Mechanical</div>

    <span class="front__tab"></span>
    <div class="person">
      <p class="person__name">Daniel Moore</p>
      <p class="person__role">Managing Director</p>
    </div>

    <ul class="contacts">
      <li>Your address<span class="icon-blank"></span></li>
      <li>City State, Zip 1234
        <svg viewBox="0 0 12 12"><path d="M2 1h3l1 3-2 1a7 7 0 0 0 3 3l1-2 3 1v3a1 1 0 0 1-1 1A10 10 0 0 1 1 2a1 1 0 0 1 1-1z" fill="#0b0b0b"/></svg>
      </li>
      <li class="spacer"></li>
      <li>123 456 789
        <svg viewBox="0 0 12 12"><rect x="1" y="2.5" width="10" height="7" fill="#0b0b0b"/><path d="M1.5 3l4.5 3.5L10.5 3" stroke="#fff" fill="none"/></svg>
      </li>
      <li>info@yourmail.com
        <svg viewBox="0 0 12 12"><circle cx="6" cy="6" r="5.5" fill="#0b0b0b"/><path d="M0.5 6h11M6 .5c2.5 3 2.5 8 0 11M6 .5c-2.5 3-2.5 8 0 11" stroke="#fff" stroke-width=".8" fill="none"/></svg>
      </li>
      <li>www.yourwebsite.com<span class="icon-blank"></span></li>
    </ul>

    <p class="ghost-name" aria-hidden="true">Cedar Ridge</p>
  </section>

</main>
</body>
</html>
```